Full 10+ Page Online Learning eBook Design - NOT just the cover :)

We currently have an eBook within the online learning space which is geared towards a consumer audience (hobbyists, interests), but we have a new 2.0 version which is geared towards professionals (certifications, training, continuing ed, career-oriented). We need a new design and need the words/copy put into the eBook, but want to keep the look and feel of the original (open to variations in design). File is attached, along with various logo options.

Target Market(s)

Professionals

Industry/Entity Type

Learning

Font styles to use
Sans Serif

Colors
33a6d7
acd036
919191

Requirements
Must have
• Must follow a very similar look a feel of the original file. We use a lot of fonts like Raleway, Gotham, Helvetica Neue, Gil Sans, DIN - anything modern looking. We also use a lot of grayish hexagons in our corporate design. Feel free to check out brightlanternhub.example to get a better sense.
Nice to have
• Include some professionally oriented icons / photos
Should not have
• No cartoonish graphics or imagery

```html
<!DOCTYPE html>
<html lang="en">
<head>
<meta charset="utf-8">
<title>The Modern Learner &amp; Content</title>
<link href="https://fonts.googleapis.com/css2?family=Raleway:wght@400;500&family=Open+Sans:wght@400&display=swap" rel="stylesheet">
<style>
  :root {
    --grey-band: #939393;
    --green: #acd036;
    --ink: #1e1e1e;
    --paper: #ffffff;
    --sky-top: #2a2436;
    --sky-mid: #4a3a4e;
    --city: #6a5a4a;
    --water: #1c2230;
  }
  html, body {
    margin: 0;
    padding: 0;
    overflow: hidden;
    background: var(--paper);
  }
  .page {
    position: relative;
    width: 852px;
    height: 1200px;
    overflow: hidden;
    background: var(--paper);
    font-family: "Open Sans", Arial, sans-serif;
    color: var(--ink);
  }
  .band {
    position: absolute;
    left: 0;
    width: 852px;
    background: var(--grey-band);
  }
  .band--top { top: 0; height: 19px; }
  .band--under-hero { top: 478px; height: 19px; }
  .band--bottom { top: 1181px; height: 19px; }
  .hero {
    position: absolute;
    top: 19px;
    left: 0;
    width: 852px;
    height: 459px;
    background:
      linear-gradient(180deg,
        var(--sky-top) 0%,
        #3a2f45 25%,
        var(--sky-mid) 45%,
        #8a6a4a 62%,
        var(--city) 68%,
        #3a3040 76%,
        var(--water) 100%);
  }
  .section-title {
    position: absolute;
    top: 520px;
    left: 6px;
    margin: 0;
    font-family: "Raleway", Arial, sans-serif;
    font-weight: 500;
    font-size: 20px;
    letter-spacing: 0.2px;
    color: var(--ink);
  }
  .title-rule {
    position: absolute;
    top: 547px;
    left: 6px;
    width: 840px;
    height: 3px;
    background: var(--green);
  }
  .body-copy {
    position: absolute;
    top: 553px;
    left: 6px;
    width: 840px;
    font-size: 14.4px;
    line-height: 18.4px;
  }
  .body-copy p {
    margin: 0 0 18.4px 0;
  }
  .case-box {
    position: absolute;
    top: 931px;
    left: 6px;
    width: 837px;
    height: 216px;
    background: var(--green);
    display: flex;
    align-items: center;
    justify-content: center;
  }
  .case-box p {
    margin: 0;
    width: 760px;
    text-align: center;
    font-family: "Raleway", Arial, sans-serif;
    font-weight: 400;
    font-size: 16.8px;
    line-height: 21px;
    color: var(--paper);
  }
</style>
</head>
<body>
<main class="page">
  <div class="band band--top"></div>
  <div class="hero" role="img" aria-label="Night skyline of a waterfront city with lit skyscrapers reflected in the river"></div>
  <div class="band band--under-hero"></div>

  <h1 class="section-title">THE MODERN LEARNER&amp; CONTENT</h1>
  <div class="title-rule"></div>

  <section class="body-copy">
    <p>Besides helping to build a business that caters to today's learners, the advantage of being able to accommodate an appetite for mobile learning is that it enables contextual learning.The student may choose to become embedded in interactive content on the job for brief, relevant bursts of learning.</p>
    <p>What does the content look like?It might include videos, audio lectures, animations, multimedia, slideshows, images and diagrams, whitepaper text, articles and book content. This kind of mixing addresses a variety of learning styles and maintains student engagement. Fortunately, the newest forms of learning technology allow you to repurpose your existing content quickly and, by dragging and dropping those assets into sequences, to create specialized courses for online delivery and monetization.</p>
    <p>Unlike the typical webinar or training manual, the content is broken into smaller chunks to help ensure retention. It uses a variety of learning types -- flash cards, hot spots, quizzes and matching -- to help to break up the monotony typically associated with online learning.</p>
    <p>We have found that short snippets of learning experience can have just as much impact on a person's understanding and retention as a multi-week or multi-month instructor-led certification program.</p>
    <p>What's important is to be able to offer your customer the ability to log in wherever they happen to be, on whatever device they're using at the moment and pick up on the learning where they last left off. That intelligent progression is an expectation of the modern learner.</p>
  </section>

  <aside class="case-box">
    <p>Ridgeway Media is a publishing company with products in arts&amp;crafts, outdoors, lifestyle and other enthusiast categories. While this long-time media organization had a number of successful online learning and video subscription sites that offered learning experiences to passionate communities in crafting, writing and web design, some of those businesses were built on myriad technology platforms established years before. Ridgeway Media wanted to consolidate on a single platform and shift its online learning to the next level. By moving to Bright Lantern Hub' Learning Business Platform, the company could quickly package and upsell ever-changing digital products within its learning environment and at the point of purchase.</p>
  </aside>

  <div class="band band--bottom"></div>
</main>
</body>
</html>
```